Company identity deisgn should support 2 languages

I would like to get our company identity design
This includes the following only
Business Cards 2 languages Arabic and English
Email signature
Letterhead
Linkedin profile images
Attached is the logo in Ai format

Requirements
Must have
• For business card
Must have
Name and Adrees in arabic
Name and Address in english
You might use both side of the card
Should not have
• Any pictures other than the logo

```html
<!DOCTYPE html>
<html lang="en">
<head>
<meta charset="utf-8">
<title>Nova Cortex Systems — Business Cards</title>
<link rel="stylesheet" href="https://fonts.googleapis.com/css2?family=Poppins:wght@400;500;600&family=Noto+Sans+Arabic:wght@400;600&display=swap">
<style>
  :root {
    --brand-blue: #1278bf;
    --rule-grey: #cfd1d3;
    --card-white: #ffffff;
    --page-bg: #dcdcdc;
    --ink-light: #ffffff;
  }
  * { margin: 0; padding: 0; box-sizing: border-box; }
  html, body { width: 1200px; height: 1200px; overflow: hidden; background: var(--page-bg); }
  body { font-family: "Poppins", sans-serif; position: relative; }

  .card {
    position: absolute;
    left: 150px;
    width: 900px;
    height: 514px;
    border-radius: 34px;
    overflow: hidden;
    background: var(--card-white);
  }
  .card--english { top: 56px; }
  .card--arabic { top: 630px; }

  .card__band { position: absolute; inset: 0; }

  .brand {
    position: absolute;
    top: 132px;
    left: 0;
    width: 100%;
    display: flex;
    justify-content: center;
    align-items: center;
    gap: 14px;
  }
  .brand__dot { width: 22px; height: 22px; border-radius: 50%; background: var(--brand-blue); }
  .brand__name {
    font-size: 32px;
    font-weight: 500;
    letter-spacing: 1px;
    color: var(--brand-blue);
    text-transform: uppercase;
  }

  .holder {
    position: absolute;
    left: 53px;
    top: 372px;
    color: var(--ink-light);
  }
  .holder__name { font-size: 29px; font-weight: 600; line-height: 1.1; }
  .holder__title { font-size: 20px; font-weight: 400; line-height: 1.3; }
  .holder__address { margin-top: 10px; font-size: 20px; line-height: 1.25; }

  .holder--arabic { font-family: "Noto Sans Arabic", "Poppins", sans-serif; top: 362px; }
  .holder--arabic .holder__name { font-size: 30px; }
  .holder--arabic .holder__address { font-size: 18px; line-height: 1.6; }
  .holder--arabic .rtl { direction: rtl; text-align: left; unicode-bidi: plaintext; }

  .contact {
    position: absolute;
    right: 36px;
    top: 380px;
    list-style: none;
    color: var(--ink-light);
    font-size: 21px;
    line-height: 26px;
  }
  .contact__item { display: flex; justify-content: flex-end; align-items: center; gap: 12px; }
  .contact__icon { width: 17px; height: 17px; flex: none; }
</style>
</head>
<body>

<section class="card card--english" aria-label="Business card, English side">
  <svg class="card__band" viewBox="0 0 900 514" aria-hidden="true">
    <rect x="0" y="306" width="900" height="7" fill="var(--rule-grey)"/>
    <rect x="0" y="313" width="900" height="201" fill="var(--brand-blue)"/>
    <polygon points="700,306 788,306 744,352" fill="var(--rule-grey)"/>
    <polygon points="709,306 779,306 744,341" fill="var(--card-white)"/>
    <circle cx="744" cy="316" r="7" fill="var(--brand-blue)"/>
  </svg>

  <div class="brand">
    <span class="brand__dot"></span>
    <span class="brand__name">Nova Cortex Systems</span>
  </div>

  <div class="holder">
    <p class="holder__name">DANIEL HARPER</p>
    <p class="holder__title">President</p>
    <p class="holder__address">1420 Willow Creek Road<br>Fairbanks, Alaska 99701</p>
  </div>

  <ul class="contact">
    <li class="contact__item">555-214-7730
      <svg class="contact__icon" viewBox="0 0 24 24"><path fill="#fff" d="M6.6 10.8a15.1 15.1 0 0 0 6.6 6.6l2.2-2.2c.3-.3.7-.4 1-.2 1.1.4 2.3.6 3.6.6.6 0 1 .4 1 1V20c0 .6-.4 1-1 1A17 17 0 0 1 3 4c0-.6.4-1 1-1h3.5c.6 0 1 .4 1 1 0 1.3.2 2.5.6 3.6.1.3 0 .7-.2 1z"/></svg></li>
    <li class="contact__item">555-408-1962
      <svg class="contact__icon" viewBox="0 0 24 24"><rect x="6" y="2" width="12" height="20" rx="2" fill="none" stroke="#fff" stroke-width="2.4"/><rect x="10" y="17" width="4" height="2" fill="#fff"/></svg></li>
    <li class="contact__item">hello@novacortex.com
      <svg class="contact__icon" viewBox="0 0 24 24"><rect x="2" y="5" width="20" height="14" fill="#fff"/><path d="M2 5l10 8 10-8" fill="none" stroke="var(--brand-blue)" stroke-width="1.8"/></svg></li>
    <li class="contact__item">www.novacortex.com
      <svg class="contact__icon" viewBox="0 0 24 24"><circle cx="12" cy="12" r="10" fill="#fff"/><path d="M7 7c2 1 3 3 2 5s1 3 0 5M15 5c-1 2 1 3 3 3M14 14c2 0 3 2 2 4" fill="none" stroke="var(--brand-blue)" stroke-width="1.8"/></svg></li>
  </ul>
</section>

<section class="card card--arabic" aria-label="Business card, Arabic side" lang="ar">
  <svg class="card__band" viewBox="0 0 900 514" aria-hidden="true">
    <rect x="0" y="306" width="900" height="7" fill="var(--rule-grey)"/>
    <rect x="0" y="313" width="900" height="201" fill="var(--brand-blue)"/>
    <polygon points="700,306 788,306 744,352" fill="var(--rule-grey)"/>
    <polygon points="709,306 779,306 744,341" fill="var(--card-white)"/>
    <circle cx="744" cy="316" r="7" fill="var(--brand-blue)"/>
  </svg>

  <div class="brand" lang="en">
    <span class="brand__dot"></span>
    <span class="brand__name">Nova Cortex Systems</span>
  </div>

  <div class="holder holder--arabic">
    <p class="holder__name rtl">دانيال هاربر</p>
    <p class="holder__title rtl">رئيس</p>
    <p class="holder__address"><span class="rtl">1420 طريق ويلو كريك</span><br><span class="rtl">فيربانكس، ألاسكا 99701</span></p>
  </div>

  <ul class="contact" lang="en" style="right:46px; top:376px;">
    <li class="contact__item">555-214-7730
      <svg class="contact__icon" viewBox="0 0 24 24"><path fill="#fff" d="M6.6 10.8a15.1 15.1 0 0 0 6.6 6.6l2.2-2.2c.3-.3.7-.4 1-.2 1.1.4 2.3.6 3.6.6.6 0 1 .4 1 1V20c0 .6-.4 1-1 1A17 17 0 0 1 3 4c0-.6.4-1 1-1h3.5c.6 0 1 .4 1 1 0 1.3.2 2.5.6 3.6.1.3 0 .7-.2 1z"/></svg></li>
    <li class="contact__item">555-408-1962
      <svg class="contact__icon" viewBox="0 0 24 24"><rect x="6" y="2" width="12" height="20" rx="2" fill="none" stroke="#fff" stroke-width="2.4"/><rect x="10" y="17" width="4" height="2" fill="#fff"/></svg></li>
    <li class="contact__item">hello@novacortex.com
      <svg class="contact__icon" viewBox="0 0 24 24"><rect x="2" y="5" width="20" height="14" fill="#fff"/><path d="M2 5l10 8 10-8" fill="none" stroke="var(--brand-blue)" stroke-width="1.8"/></svg></li>
    <li class="contact__item">www.novacortex.com
      <svg class="contact__icon" viewBox="0 0 24 24"><circle cx="12" cy="12" r="10" fill="#fff"/><path d="M7 7c2 1 3 3 2 5s1 3 0 5M15 5c-1 2 1 3 3 3M14 14c2 0 3 2 2 4" fill="none" stroke="var(--brand-blue)" stroke-width="1.8"/></svg></li>
  </ul>
</section>

</body>
</html>
```